Fastest Work at home Solution for Small Businesses

We need a web page for a product called *BrightReed*
We develop an innovative VPN Appliance (Model-Name ->Reed Alpha) that gives small business the possibility literally setup the possibility for Companies to let their employees work from home.
With our secure appliance we create safe connection between any business and the employee *working at home*
Our Products *Reed Alpha* are rolled out in minutes.
A. Employees can connect directly
B. Work from any location
C. All this without having to change the company firewall
Use case
=======
1. Go to our page
2. Select Product
3. Order
4. Connect to any Switch in the company
5. install software on employees laptop
***** INSTANT Connection ******
Target Market(s)
Businesses
Coding
Coded - Design and coding required
Number of Pages Required
3 page
Font styles to use
Look and feel
Each slider illustrates characteristics of the customer's brand and the style your logo design should communicate.

```html
<!DOCTYPE html>
<html lang="en">
<head>
<meta charset="utf-8">
<title>BrightReed – Fastest Work at home Solution for Small Businesses</title>
<link rel="stylesheet" href="https://fonts.googleapis.com/css2?family=Jost:wght@400;500&display=swap">
<style>
:root{
  --navy:#0b3aa4;
  --deep:#0a2a78;
  --sky:#4cc6f4;
  --sky-soft:#6fd3f7;
  --text:#333a44;
  --muted:#5b6470;
  --band:#f5f5f5;
  --footer:#1148bf;
  --white:#ffffff;
}
*{margin:0;padding:0;box-sizing:border-box}
html,body{width:1200px;height:4183px;overflow:hidden}
body{position:relative;font-family:"Jost",sans-serif;color:var(--text);background:var(--white)}
.abs{position:absolute}

/* header */
.site-header{position:absolute;left:0;top:0;width:1200px;height:130px;background:var(--white)}
.brand{position:absolute;display:flex;align-items:center;gap:10px;font-weight:500;color:var(--deep)}
.brand-mark{width:30px;height:30px;background:var(--navy);border-radius:4px}
.site-header .brand{left:110px;top:44px;font-size:40px;line-height:44px}
.main-nav a{position:absolute;top:56px;font-size:17px;color:#2a2f38;text-decoration:none}
.main-nav a.active{color:var(--navy)}

/* hero */
.hero{position:absolute;left:0;top:130px;width:1200px;height:727px;background:linear-gradient(135deg,#4a5d75 0%,#5d6f86 40%,#3e4e61 100%)}
.hero-title{position:absolute;left:724px;top:420px;font-size:33px;line-height:50px;color:var(--white);font-weight:400}
.hero-edge{position:absolute;left:0;top:0}

/* section headings */
.section-title{position:absolute;left:0;width:1200px;text-align:center;font-size:46px;font-weight:500;color:var(--navy)}
.section-title span{color:var(--sky)}
.rule{position:absolute;height:2px;width:40px;background:var(--sky)}
.rule.center{left:580px}

/* products */
.illustration{position:absolute;border-radius:12px;background:linear-gradient(160deg,#e6e9fb,#c9cdf2 60%,#f5d6de)}
.feature-title{position:absolute;font-size:29px;line-height:35px;font-weight:400;color:var(--navy)}
.feature-text{position:absolute;width:500px;font-size:14.6px;line-height:32px;color:var(--muted)}
.btn-outline{position:absolute;width:155px;height:54px;border:2px solid var(--navy);border-radius:27px;color:var(--sky);font-size:18px;display:flex;align-items:center;justify-content:center;text-decoration:none}
.connector{position:absolute;left:0;top:0}

/* promo band */
.promo{position:absolute;left:0;top:2113px;width:1200px;height:497px;background:linear-gradient(90deg,#0a3ea8 0%,#1a63d4 45%,#3aa0ea 75%,#5cc8f6 100%)}
.promo-title{position:absolute;left:112px;top:110px;font-size:29px;line-height:45px;color:var(--white);font-weight:400}
.promo-text{position:absolute;left:112px;top:220px;width:500px;font-size:14.6px;line-height:30px;color:#e8efff}
.btn-fill{position:absolute;left:112px;top:336px;width:158px;height:54px;border-radius:27px;background:var(--sky);color:var(--white);font-size:18px;display:flex;align-items:center;justify-content:center;text-decoration:none}

/* steps */
.step-icon{position:absolute;width:141px;height:141px;border-radius:50%;display:flex;align-items:center;justify-content:center}
.step-label{position:absolute;width:200px;text-align:center;font-size:21px;line-height:28px;color:#3a3f47}
.btn-instant{position:absolute;left:474px;top:3193px;width:250px;height:61px;border:2px solid var(--navy);border-radius:31px;color:var(--navy);font-size:18px;font-weight:500;display:flex;align-items:center;justify-content:center;text-decoration:none}

/* blog */
.blog{position:absolute;left:0;top:3305px;width:1200px;height:560px;background:var(--band)}
.post{position:absolute;top:3440px;width:314px}
.post-image{width:314px;height:238px}
.post-date{position:absolute;left:11px;top:211px;width:292px;height:40px;background:var(--band);text-align:center;font-size:19px;line-height:48px;color:var(--navy)}
.post-text{margin-top:22px;text-align:center;font-size:15px;line-height:26px;color:var(--muted)}

/* footer */
.footer-shape{position:absolute;left:0;top:3800px}
.site-footer .brand{left:0;width:1200px;justify-content:center;top:3908px;font-size:48px;line-height:52px;color:var(--white)}
.site-footer .brand-mark{background:var(--white);width:34px;height:34px}
.footer-nav a{position:absolute;top:3994px;font-size:17px;color:var(--white);text-decoration:none}
.social{position:absolute;top:4050px;width:36px;height:36px;border:2px solid var(--white);border-radius:50%}
.copyright{position:absolute;left:0;width:1200px;top:4112px;text-align:center;font-size:14px;color:#dfe8ff}
</style>
</head>
<body>

<header class="site-header">
  <div class="brand"><span class="brand-mark"></span>BrightReed</div>
  <nav class="main-nav">
    <a class="active" href="#" style="left:447px">Home</a>
    <a href="#" style="left:544px">About Us</a>
    <a href="#" style="left:664px">Products</a>
    <a href="#" style="left:781px">How it work</a>
    <a href="#" style="left:922px">Blog</a>
    <a href="#" style="left:1008px">Contact Us</a>
  </nav>
</header>

<section class="hero" role="img" aria-label="Photo of a woman working on a laptop and phone at home on a sofa">
  <h1 class="hero-title">Fastest Work at home<br>Solution for Small Businesses</h1>
  <svg class="hero-edge" width="1200" height="727" viewBox="0 0 1200 727">
    <polygon points="690,670 1200,630 1200,715" fill="#4cc6f4"/>
    <polygon points="0,727 690,670 1200,715 1200,727" fill="#ffffff"/>
  </svg>
</section>

<h2 class="section-title" style="top:862px">Our <span>Products</span></h2>
<div class="rule center" style="top:931px"></div>

<svg class="connector" width="1200" height="2100" viewBox="0 0 1200 2100" fill="none" stroke="#8a8f99" stroke-width="2" stroke-dasharray="6 7">
  <path d="M302 1290 V1335 Q302 1357 325 1357 H820 Q876 1357 876 1400"/>
  <path d="M878 1640 V1688 Q878 1710 855 1710 H360 Q335 1710 332 1755"/>
</svg>

<div class="illustration" style="left:187px;top:991px;width:211px;height:292px" role="img" aria-label="Isometric illustration of two employees at desks connected to a cloud"></div>
<h3 class="feature-title" style="left:500px;top:1000px">Employees can connect directly</h3>
<div class="rule" style="left:502px;top:1048px"></div>
<p class="feature-text" style="left:502px;top:1073px">Sed ut perspiciatis unde omnis iste natus error sit voluptatem accusantiu doloremque laudantium, totam rem aperiam, eaque ipsa quae ab illo in vent et quasi architecto beatae vitae dicta sunt explicabo.</p>
<a class="btn-outline" href="#" style="left:503px;top:1197px">Read More</a>

<div class="illustration" style="left:796px;top:1356px;width:211px;height:268px" role="img" aria-label="Isometric illustration of a network of remote workers around a desk"></div>
<h3 class="feature-title" style="left:197px;top:1422px">Work from any location</h3>
<div class="rule" style="left:199px;top:1470px"></div>
<p class="feature-text" style="left:199px;top:1495px">Sed ut perspiciatis unde omnis iste natus error sit voluptatem accusantiu doloremque laudantium, totam rem aperiam, eaque ipsa quae ab illo in vent et quasi architecto beatae vitae dicta sunt explicabo.</p>
<a class="btn-outline" href="#" style="left:200px;top:1619px">Read More</a>

<div class="illustration" style="left:182px;top:1770px;width:216px;height:260px" role="img" aria-label="Isometric illustration of a person working in an armchair on a phone with a folder above"></div>
<h3 class="feature-title" style="left:500px;top:1755px">All this without having to change the<br>company firewall</h3>
<div class="rule" style="left:502px;top:1846px"></div>
<p class="feature-text" style="left:502px;top:1872px">Sed ut perspiciatis unde omnis iste natus error sit voluptatem accusantiu doloremque laudantium, totam rem aperiam, eaque ipsa quae ab illo in vent et quasi architecto beatae vitae dicta sunt explicabo.</p>
<a class="btn-outline" href="#" style="left:503px;top:1994px">Read More</a>

<section class="promo" role="img" aria-label="Blue-tinted photo of a woman using a laptop">
  <h2 class="promo-title">Sed ut perspiciatis unde<br>iste natus error sit voluptatem accusan</h2>
  <p class="promo-text">Nemo enim ipsam voluptatem quia voluptas sit aspernatur aut odit aut fugit, sed quia consequuntur magni dolores eos qui ratione voluptate ipsam voluptatem &nbsp;sequi nesciunt.</p>
  <a class="btn-fill" href="#">Read More</a>
</section>

<h2 class="section-title" style="top:2670px">How <span>it Works</span></h2>
<div class="rule center" style="top:2738px"></div>

<div class="step-icon" style="left:131px;top:2801px;background:linear-gradient(180deg,#6ad6f8,#2ba6ec)">
  <svg width="70" height="60" viewBox="0 0 70 60" fill="none" stroke="#fff" stroke-width="3"><rect x="3" y="3" width="64" height="54" rx="3"/><line x1="3" y1="15" x2="67" y2="15"/><rect x="14" y="26" width="16" height="20"/><line x1="38" y1="28" x2="56" y2="28"/><line x1="38" y1="36" x2="56" y2="36"/><line x1="38" y1="44" x2="56" y2="44"/></svg>
</div>
<div class="step-label" style="left:101px;top:2950px">Go to our page</div>

<div class="step-icon" style="left:333px;top:2923px;background:linear-gradient(180deg,#3b8fe0,#1c5fc4)">
  <svg width="70" height="70" viewBox="0 0 70 70" fill="none" stroke="#fff" stroke-width="3"><path d="M35 4 V26 M27 12 L35 4 L43 12"/><path d="M10 36 L35 26 L60 36 L35 46 Z"/><path d="M10 36 V56 L35 66 L60 56 V36"/><line x1="35" y1="46" x2="35" y2="66"/></svg>
</div>
<div class="step-label" style="left:303px;top:3072px">Select Product</div>

<div class="step-icon" style="left:531px;top:2801px;background:linear-gradient(180deg,#1f59c8,#0d3aa0)">
  <svg width="72" height="64" viewBox="0 0 72 64" fill="none" stroke="#fff" stroke-width="3"><rect x="3" y="3" width="66" height="44" rx="3"/><line x1="26" y1="60" x2="46" y2="60"/><line x1="36" y1="47" x2="36" y2="60"/><rect x="26" y="20" width="20" height="16"/><path d="M30 20 V14 a6 6 0 0 1 12 0 V20"/></svg>
</div>
<div class="step-label" style="left:501px;top:2950px">Order</div>

<div class="step-icon" style="left:731px;top:2923px;background:linear-gradient(180deg,#1a4fb4,#0c2f86)">
  <svg width="70" height="64" viewBox="0 0 70 64" fill="none" stroke="#fff" stroke-width="3"><circle cx="10" cy="54" r="6"/><circle cx="26" cy="32" r="6"/><circle cx="44" cy="44" r="6"/><circle cx="60" cy="10" r="6"/><line x1="14" y1="49" x2="22" y2="37"/><line x1="31" y1="35" x2="39" y2="41"/><line x1="47" y1="39" x2="57" y2="16"/></svg>
</div>
<div class="step-label" style="left:701px;top:3072px">Connect to<br>any Switch in<br>the company</div>

<div class="step-icon" style="left:930px;top:2801px;background:linear-gradient(180deg,#133a86,#081d52)">
  <svg width="70" height="66" viewBox="0 0 70 66" fill="none" stroke="#fff" stroke-width="3"><rect x="3" y="14" width="64" height="38" rx="3"/><line x1="25" y1="62" x2="45" y2="62"/><line x1="35" y1="52" x2="35" y2="62"/><circle cx="35" cy="16" r="10" fill="#0f2f72"/><path d="M35 10 V22 M30 18 L35 22 L40 18"/></svg>
</div>
<div class="step-label" style="left:900px;top:2950px">Install software<br>on employees<br>laptop</div>

<a class="btn-instant" href="#">INSTANT Connection</a>

<section class="blog">
  <h2 class="section-title" style="top:47px">Latest <span>Blog</span></h2>
  <div class="rule center" style="top:102px"></div>
</section>

<article class="post" style="left:110px">
  <div class="post-image" role="img" aria-label="Photo of a woman using a phone beside a laptop" style="background:linear-gradient(160deg,#d9dde2,#8e9aa8)"></div>
  <div class="post-date">08 Jan 2020</div>
  <p class="post-text">Sed ut perspiciatis unde omnis iste<br>natus error sit voluptate</p>
</article>
<article class="post" style="left:443px">
  <div class="post-image" role="img" aria-label="Photo of hands typing on a laptop keyboard" style="background:linear-gradient(160deg,#b7c3cf,#4b5866)"></div>
  <div class="post-date">08 Jan 2020</div>
  <p class="post-text">Sed ut perspiciatis unde omnis iste<br>natus error sit voluptate</p>
</article>
<article class="post" style="left:776px">
  <div class="post-image" role="img" aria-label="Photo of a man working at a laptop with notebooks" style="background:linear-gradient(160deg,#e4e0d8,#7c7f86)"></div>
  <div class="post-date">08 Jan 2020</div>
  <p class="post-text">Sed ut perspiciatis unde omnis iste<br>natus error sit voluptate</p>
</article>

<footer class="site-footer">
  <svg class="footer-shape" width="1200" height="383" viewBox="0 0 1200 383">
    <polygon points="0,16 1200,16 1200,383 0,383" fill="#1148bf"/>
    <polygon points="0,0 1200,60 1200,383 0,383" fill="#1148bf"/>
    <polygon points="0,0 520,0 1200,60 1200,0" fill="#f5f5f5"/>
    <polygon points="780,16 1200,0 1200,80" fill="#4cc6f4"/>
  </svg>
  <div class="brand"><span class="brand-mark"></span>BrightReed</div>
  <nav class="footer-nav">
    <a href="#" style="left:279px">Home</a>
    <a href="#" style="left:375px">About Us</a>
    <a href="#" style="left:496px">Products</a>
    <a href="#" style="left:613px">How it work</a>
    <a href="#" style="left:755px">Blog</a>
    <a href="#" style="left:841px">Contact Us</a>
  </nav>
  <a class="social" href="#" aria-label="Social profile 1" style="left:495px"></a>
  <a class="social" href="#" aria-label="Social profile 2" style="left:539px"></a>
  <a class="social" href="#" aria-label="Social profile 3" style="left:581px"></a>
  <a class="social" href="#" aria-label="Social profile 4" style="left:625px"></a>
  <a class="social" href="#" aria-label="Social profile 5" style="left:667px"></a>
  <p class="copyright">© Copyrights 2021- BrightReed. All Rights Reserved.</p>
</footer>

</body>
</html>
```